Animal Eye Clinic needs a Business card

We are a new veterinary ophthalmology practice (Ridgeline Pet Vision Care) and we need a business card designed. We only see animal eyes - we are not a regular veterinary clinic. We already have a logo. We are looking for a professional, good looking business card to hand out to our clients. We are looking for something simple but professional and contemporary. Our logo is likely the only picture/graphic that needs to be on the card.
Updates

Contact Information for Business Card

Delia Vossman, BSc, DVM, MSc, DipACVO
Veterinary Ophthalmologist

Phone: 250.418.3927
Email: ridgelinepetvisioncare@mailbox-example.net
Website: ridgelinepetvisioncare-example.net
Address: 1874 Thornbury Rd
Kelowna, BC, V1X 4M9

Colors

Designer to choose colors to be used in the design.

Requirements
Must have
• Our logo (attached)

```html
<!DOCTYPE html>
<html lang="en">
<head>
<meta charset="utf-8">
<title>Ridgeline Pet Vision Care – Business Card</title>
<link rel="stylesheet" href="https://fonts.googleapis.com/css2?family=Lato:wght@300;400;700;900&display=swap">
<style>
  :root {
    --teal: #1a9eae;
    --teal-dark: #13899a;
    --teal-soft: #4fb9c6;
    --ink: #4a4a4a;
    --grey-swoosh: #8a8a8a;
    --paper: #ffffff;
    --backdrop: #2b2b2b;
  }
  * { margin: 0; padding: 0; box-sizing: border-box; }
  html, body {
    width: 1200px; height: 900px; overflow: hidden;
    background: var(--backdrop);
    font-family: "Lato", sans-serif;
  }
  .canvas { position: relative; width: 1200px; height: 900px; }

  .card {
    position: absolute;
    width: 560px; height: 320px;
    border-radius: 18px;
    overflow: hidden;
  }

  /* Reverse side */
  .card--back { left: 150px; top: 100px; background: var(--teal); }
  .card--back .pattern-area {
    position: absolute; inset: 0;
    background: linear-gradient(135deg, var(--teal) 0%, var(--teal-soft) 50%, var(--teal) 100%);
    opacity: .55;
  }
  .card--back .brand {
    position: absolute; left: 0; right: 0; top: 128px;
    display: flex; align-items: center; justify-content: center; gap: 14px;
  }
  .brand__dot {
    width: 34px; height: 34px; border-radius: 50%;
    background: var(--ink);
  }
  .card--back .brand__name {
    font-weight: 900; font-size: 27px; letter-spacing: .5px;
    color: var(--ink); text-transform: uppercase;
  }
  .card--back .website {
    position: absolute; left: 0; right: 0; top: 208px;
    text-align: center;
    font-size: 12px; letter-spacing: 2.5px; color: var(--ink);
  }

  /* Front side */
  .card--front { left: 490px; top: 470px; background: var(--paper); }
  .card--front svg.waves { position: absolute; inset: 0; }
  .card--front .brand {
    position: absolute; left: 96px; top: 86px;
    display: flex; align-items: center; gap: 12px;
  }
  .card--front .brand__dot { background: var(--teal); width: 28px; height: 28px; }
  .card--front .brand__name {
    font-weight: 900; font-size: 21px; color: var(--teal);
    text-transform: uppercase; letter-spacing: .4px;
  }
  .person {
    position: absolute; right: 28px; top: 128px;
    text-align: right; color: var(--paper);
  }
  .person__name { font-weight: 900; font-size: 16px; text-transform: uppercase; }
  .person__credentials { font-weight: 300; font-size: 12px; margin-top: 3px; }
  .person__title { font-weight: 700; font-size: 13px; margin-top: 3px; }

  .contact {
    position: absolute; left: 30px; bottom: 26px;
    list-style: none; color: var(--paper); font-size: 12.5px;
  }
  .contact li { display: flex; align-items: center; gap: 9px; margin-top: 5px; }
  .contact svg { width: 13px; height: 13px; fill: var(--paper); flex: none; }
  .contact .address { font-weight: 700; font-size: 13.5px; padding-left: 22px; }
</style>
</head>
<body>
<main class="canvas">

  <section class="card card--back" aria-label="Business card, reverse side">
    <div class="pattern-area" role="img" aria-label="Repeating paw print pattern"></div>
    <div class="brand">
      <span class="brand__dot"></span>
      <span class="brand__name">Ridgeline Pet Vision Care</span>
    </div>
    <p class="website">www.ridgelinepetvisioncare-example.net</p>
  </section>

  <section class="card card--front" aria-label="Business card, front side">
    <svg class="waves" viewBox="0 0 560 320" preserveAspectRatio="none" aria-hidden="true">
      <circle cx="420" cy="70" r="95" fill="#1a9eae" opacity=".08"/>
      <path d="M0 320 L0 262 C110 190 280 130 560 118 L560 320 Z" fill="#1a9eae"/>
      <path d="M140 245 C250 170 370 130 440 122 C360 140 240 185 150 250 Z" fill="#8a8a8a"/>
    </svg>

    <div class="brand">
      <span class="brand__dot"></span>
      <span class="brand__name">Ridgeline Pet Vision Care</span>
    </div>

    <div class="person">
      <p class="person__name">Delia Vossman</p>
      <p class="person__credentials">BSc, DVM, MSc, DipACVO</p>
      <p class="person__title">Veterinary Ophthalmologist</p>
    </div>

    <ul class="contact">
      <li>
        <svg viewBox="0 0 24 24"><path d="M6.6 10.8a15.1 15.1 0 0 0 6.6 6.6l2.2-2.2c.3-.3.7-.4 1-.2 1.1.4 2.3.6 3.6.6.6 0 1 .4 1 1V20c0 .6-.4 1-1 1A17 17 0 0 1 3 4c0-.6.4-1 1-1h3.5c.6 0 1 .4 1 1 0 1.3.2 2.5.6 3.6.1.3 0 .7-.2 1z"/></svg>
        250.418.3927
      </li>
      <li>
        <svg viewBox="0 0 24 24"><path d="M2 5h20v14H2zm2 2v.5l8 5 8-5V7l-8 5z"/></svg>
        ridgelinepetvisioncare@mailbox-example.net
      </li>
      <li class="address">1874 Thornbury Rd, Kelowna, BC, V1X 4M9</li>
    </ul>
  </section>

</main>
</body>
</html>
```